Business Card Design

New business card design

Target Market(s)

Residential & Commercial Property Managers

Industry/Entity Type

Plumbing Services

Contact Information for Business Card

Name - Rowan Keddle, title - Director, Phone Number - 0431 286 517, email - rowan@tbk-plumbing.com.au, Company ABN - 73 215 904 386,

Font styles to use
Sans Serif

Colors
0054AA
0677BA
7BADD7
CADEEF
E8F1F8

```html
<!DOCTYPE html>
<html lang="en">
<head>
<meta charset="utf-8">
<title>TBK Plumbing Services – Business Card</title>
<link href="https://fonts.googleapis.com/css2?family=Montserrat:wght@400;500;700&display=swap" rel="stylesheet">
<style>
  :root {
    --sky: #29a8e0;
    --ink: #1e2530;
    --paper: #ffffff;
    --stage: #e8f1f8;
    --muted: #7a6a60;
  }
  * { margin: 0; padding: 0; box-sizing: border-box; }
  html, body { width: 1200px; height: 931px; overflow: hidden; }
  body {
    background: var(--stage);
    font-family: "Montserrat", sans-serif;
    color: var(--ink);
    position: relative;
  }
  .card {
    position: absolute;
    width: 620px;
    height: 354px;
    border-radius: 22px;
    overflow: hidden;
    box-shadow: 0 10px 28px rgba(30, 37, 48, 0.18);
  }
  .card--back { left: 80px; top: 70px; background: var(--sky); }
  .card--front { left: 500px; top: 500px; background: var(--paper); }

  .wordmark {
    position: absolute;
    display: flex;
    align-items: center;
    gap: 14px;
    color: var(--ink);
    font-weight: 500;
  }
  .wordmark__dot { width: 22px; height: 22px; border-radius: 50%; flex: none; }
  .wordmark__text { display: flex; flex-direction: column; line-height: 1; }
  .wordmark__name { font-size: 96px; letter-spacing: 2px; }
  .wordmark__sub { font-size: 13px; letter-spacing: 9px; margin-top: 6px; padding-left: 4px; }

  .card--back .wordmark { left: 50%; top: 50%; transform: translate(-50%, -50%); }
  .card--back .wordmark__dot { background: var(--paper); }

  .card--front .wordmark { right: 44px; top: 28px; }
  .card--front .wordmark__name { font-size: 72px; }
  .card--front .wordmark__sub { font-size: 10px; letter-spacing: 7px; }
  .card--front .wordmark__dot { background: var(--sky); width: 18px; height: 18px; }

  .divider {
    position: absolute;
    left: 40px; right: 50px; top: 206px;
    height: 2px; background: var(--ink);
  }
  .person { position: absolute; left: 40px; top: 150px; }
  .person__name { font-size: 30px; font-weight: 700; line-height: 1.1; }
  .person__title { font-size: 16px; font-weight: 400; }

  .address {
    position: absolute; right: 50px; top: 158px;
    font-size: 14px; line-height: 1.3; text-align: right;
  }

  .contacts { position: absolute; left: 48px; top: 224px; list-style: none; }
  .contacts li {
    display: flex; align-items: center; gap: 12px;
    font-size: 15px; height: 28px;
  }
  .contacts svg { width: 16px; height: 16px; fill: var(--sky); flex: none; }

  .band {
    position: absolute; left: 0; bottom: 0;
    width: 450px; height: 14px; background: var(--sky);
  }
  .abn {
    position: absolute; right: 0; bottom: 0;
    width: 166px; height: 52px; background: var(--ink);
    color: var(--paper); font-size: 14px;
    display: flex; align-items: center; justify-content: center;
  }
  .abn__label { color: var(--sky); font-weight: 700; margin-right: 4px; }
</style>
</head>
<body>

<section class="card card--back" aria-label="Card back">
  <div class="wordmark">
    <span class="wordmark__text">
      <span class="wordmark__name">tbk</span>
      <span class="wordmark__sub">plumbing services</span>
    </span>
    <span class="wordmark__dot"></span>
  </div>
</section>

<section class="card card--front" aria-label="Card front">
  <div class="wordmark">
    <span class="wordmark__text">
      <span class="wordmark__name">tbk</span>
      <span class="wordmark__sub">plumbing services</span>
    </span>
    <span class="wordmark__dot"></span>
  </div>

  <div class="person">
    <p class="person__name">Rowan Keddle</p>
    <p class="person__title">Director</p>
  </div>

  <p class="address">48 Harbour Street<br>Wollongong NSW 2500</p>

  <div class="divider"></div>

  <ul class="contacts">
    <li>
      <svg viewBox="0 0 24 24" aria-hidden="true"><path d="M6.6 10.8a15 15 0 0 0 6.6 6.6l2.2-2.2a1 1 0 0 1 1-.25 11.4 11.4 0 0 0 3.6.57 1 1 0 0 1 1 1V20a1 1 0 0 1-1 1A17 17 0 0 1 3 4a1 1 0 0 1 1-1h3.5a1 1 0 0 1 1 1c0 1.25.2 2.45.57 3.57a1 1 0 0 1-.25 1z"/></svg>
      0431 286 517
    </li>
    <li>
      <svg viewBox="0 0 24 24" aria-hidden="true"><path d="M2 5h20v14H2z M2 5l10 8 10-8" /></svg>
      rowan@tbk-plumbing.com.au
    </li>
    <li>
      <svg viewBox="0 0 24 24" aria-hidden="true"><circle cx="12" cy="12" r="10"/></svg>
      www.tbk-plumbing.com.au
    </li>
  </ul>

  <div class="band"></div>
  <div class="abn"><span class="abn__label">ABN</span> - 73 215 904 386</div>
</section>

</body>
</html>
```